Kestrada LLC, needs a web page no more than 5 pages (for now)

Kestrada is a general contractor. Our services include general contracting, design-build construction, disaster recovery and environmental remediation. Our main clients are PMX, TQ, State and Local Gov't Agencies, Hospitals and Schools. Kestrada is also a SDVOSB.

```html
<!DOCTYPE html>
<html lang="en">
<head>
<meta charset="utf-8">
<title>Kestrada LLC – Building Trust, Delivering Value</title>
<link rel="stylesheet" href="https://fonts.googleapis.com/css2?family=Montserrat:wght@400;500;600;700&family=Unbounded:wght@800;900&display=swap">
<style>
:root{
  --gold:#b88e33;
  --beige:#ece0c8;
  --ink:#111111;
  --text:#555555;
  --field:#f5f5f5;
  --white:#ffffff;
  --footer:#0b0b0b;
  --rule:#d8d8d8;
  --footer-rule:#333333;
}
*{margin:0;padding:0;box-sizing:border-box}
html,body{width:1200px;height:3548px;overflow:hidden}
body{position:relative;background:var(--white);font-family:"Montserrat",sans-serif;color:var(--ink)}
a{text-decoration:none}
.abs{position:absolute}
.display{font-family:"Unbounded",sans-serif;font-weight:900;letter-spacing:1px;color:var(--ink);text-transform:uppercase;line-height:1;white-space:nowrap}
.section-title{font-size:31px}
.eyebrow{font-size:15px;font-weight:600;color:var(--gold);text-transform:uppercase}
.underline{width:48px;height:3px;background:var(--gold)}
.btn{display:flex;align-items:center;justify-content:center;font-size:12.5px;font-weight:600;color:var(--white);background:var(--gold)}
.btn.dark{background:var(--ink)}
.center{left:0;width:1200px;text-align:center}

.hero{left:0;top:0;width:1200px;height:798px;background:linear-gradient(180deg,#a9cad3 0%,#c9d6d8 25%,#e4c3bd 42%,#b88a78 55%,#4a3a35 75%,#2c2624 100%)}
.topbar{left:74px;top:22px;width:1051px;height:77px;background:var(--white);display:flex;align-items:center;padding:0 30px 0 24px}
.brand{display:flex;align-items:center;gap:8px;font-weight:700;font-size:21px;color:var(--gold)}
.brand .dot{width:14px;height:14px;border-radius:50%;background:var(--gold)}
.nav{display:flex;gap:33px;margin-left:auto;font-size:12.5px;color:#555}
.lang{display:flex;align-items:center;gap:10px;margin-left:44px;font-size:12.5px;color:#555}
.topbar .btn{margin-left:28px;width:119px;height:34px}
.hero-title{top:178px;font-size:84px;letter-spacing:3px}
.hero-sub{top:262px;font-size:42px;letter-spacing:1.5px}
.hero-text{top:314px;font-size:12.5px;line-height:19px;color:#222}

.service-item{font-size:15px;font-weight:600}
.field{background:var(--field);font-size:11px;color:#888;padding:13px 22px}
.client-label{font-size:12.5px;font-weight:600;color:var(--white);line-height:18px;text-align:center;width:200px}
.bullet{display:inline-block;width:8px;height:8px;border-radius:50%;background:var(--gold);margin-right:12px}
.footer-col{font-size:12px;line-height:22.4px}
.footer-head{font-size:15px;color:var(--white);border-left:2px solid var(--gold);padding-left:6px;margin-left:-8px;margin-bottom:8px}
</style>
</head>
<body>

<section class="abs hero" role="img" aria-label="City skyline of high-rise buildings and construction cranes at sunset"></section>
<header class="abs topbar">
  <div class="brand"><span class="dot"></span>Kestrada</div>
  <nav class="nav"><span>Home</span><span>About Us</span><span>Our Services</span><span>Clients</span><span>Certifications</span></nav>
  <div class="lang">
    <svg width="28" height="28" viewBox="0 0 28 28" aria-hidden="true"><defs><clipPath id="flag"><circle cx="14" cy="14" r="13"/></clipPath></defs><g clip-path="url(#flag)"><rect width="28" height="10" fill="#111"/><rect y="10" width="28" height="9" fill="#d00"/><rect y="19" width="28" height="9" fill="#ffce00"/></g><circle cx="14" cy="14" r="13" fill="none" stroke="#ddd"/></svg>
    DE
  </div>
  <div class="btn">Contact Us</div>
</header>
<h1 class="abs center display hero-title">Building</h1>
<p class="abs center display hero-sub">Trust Delivering Value.</p>
<p class="abs center hero-text">Kestrada is a Service-Disabled Veteran-Owned Small Business (SDVOSB) providing full-service construction solutions —<br>from design-build projects to disaster recovery and environmental remediation.</p>
<a class="abs btn" style="left:478px;top:369px;width:117px;height:33px">Learn More</a>
<a class="abs btn dark" style="left:605px;top:369px;width:116px;height:33px">Contact Us</a>

<!-- about -->
<div class="abs" style="left:147px;top:941px;width:441px;height:280px;background:var(--beige)"></div>
<div class="abs" style="left:163px;top:900px;width:469px;height:306px;background:linear-gradient(135deg,#8fa9bf,#c9a26a 55%,#6b5848)" role="img" aria-label="Two engineers in hard hats reviewing blueprints beside a glass high-rise"></div>
<p class="abs eyebrow" style="left:686px;top:926px">About Us</p>
<h2 class="abs display section-title" style="left:686px;top:950px">Who We Are</h2>
<div class="abs underline" style="left:686px;top:990px"></div>
<p class="abs" style="left:686px;top:1012px;width:375px;font-size:12.5px;line-height:19px;color:var(--text)">Kestrada is a trusted general contractor serving federal, state, and local government agencies as well as hospitals, schools, and institutions across the U.S. With a strong foundation in construction excellence and a commitment to integrity, we deliver projects that meet the highest standards of safety, quality, and compliance.</p>
<a class="abs btn" style="left:686px;top:1142px;width:117px;height:33px">Read More</a>

<!-- services -->
<p class="abs center eyebrow" style="top:1308px">Our Service</p>
<h2 class="abs center display section-title" style="top:1332px">What We Do</h2>
<div class="abs underline" style="left:576px;top:1373px"></div>
<div class="abs" style="left:74px;top:1437px;width:428px;height:95px;background:var(--gold);padding:20px 24px;color:var(--white)">
  <p style="font-size:16px;font-weight:600">GENERAL CONTRACTING</p>
  <p style="font-size:12.5px;line-height:19px;margin-top:4px">Full-spectrum construction management ensuring projects are delivered on time and on budget.</p>
</div>
<p class="abs service-item" style="left:98px;top:1560px">BUILD CONSTRUCTION</p>
<div class="abs" style="left:74px;top:1604px;width:430px;height:1px;background:var(--rule)"></div>
<p class="abs service-item" style="left:99px;top:1632px">ENVIRONMENTAL REMEDIATION</p>
<div class="abs" style="left:74px;top:1676px;width:430px;height:1px;background:var(--rule)"></div>
<p class="abs service-item" style="left:99px;top:1703px">DISASTER RECOVERY</p>
<div class="abs" style="left:648px;top:1455px;width:478px;height:280px;background:var(--beige)"></div>
<div class="abs" style="left:599px;top:1414px;width:510px;height:306px;background:linear-gradient(135deg,#d9d2c6,#b59a74 55%,#8a7456)" role="img" aria-label="Site engineer and manager discussing plans at a construction site"></div>

<!-- clients -->
<section class="abs" style="left:0;top:1827px;width:1200px;height:386px;background:linear-gradient(180deg,#b98d34,#c09a48)" role="img" aria-label="Gold-toned construction scaffolding backdrop"></section>
<p class="abs center eyebrow" style="top:1888px;color:var(--white)">Clients</p>
<h2 class="abs center display section-title" style="top:1912px;color:var(--white)">Who We Serve</h2>
<svg class="abs" style="left:0;top:1977px" width="1200" height="130" aria-hidden="true">
  <g fill="#f2efe8" stroke="#fff" stroke-width="3">
    <circle cx="192" cy="62" r="61"/><circle cx="395" cy="62" r="61"/><circle cx="599" cy="62" r="61"/><circle cx="803" cy="62" r="61"/><circle cx="1006" cy="62" r="61"/>
  </g>
  <circle cx="192" cy="62" r="46" fill="#2b4a8a"/><circle cx="395" cy="62" r="46" fill="#3a3f70"/><circle cx="599" cy="62" r="46" fill="#2b4a8a"/><circle cx="803" cy="62" r="46" fill="#6c7480"/><circle cx="1006" cy="62" r="46" fill="#1f8a4c"/>
</svg>
<p class="abs client-label" style="left:92px;top:2110px">PMX</p>
<p class="abs client-label" style="left:295px;top:2110px">TQ</p>
<p class="abs client-label" style="left:499px;top:2110px">STATE &amp; LOCAL<br>GOVERNMENT AGENCIES</p>
<p class="abs client-label" style="left:703px;top:2110px">HOSPITALS &amp; HEALTH<br>CARE FACILITIES</p>
<p class="abs client-label" style="left:896px;top:2110px;width:220px">SCHOOLS &amp; EDUCATIONAL<br>INSTITUTIONS</p>

<!-- credentials -->
<div class="abs" style="left:127px;top:2302px;width:441px;height:399px;background:linear-gradient(135deg,#b8563a,#d9a070 50%,#e57a2c)" role="img" aria-label="Smiling construction worker in hard hat and safety vest holding a clipboard"></div>
<p class="abs eyebrow" style="left:628px;top:2344px">Certifications</p>
<h2 class="abs display section-title" style="left:628px;top:2368px">Our Credentials</h2>
<div class="abs underline" style="left:628px;top:2410px"></div>
<p class="abs" style="left:628px;top:2430px;width:445px;font-size:12.5px;line-height:19px;color:var(--text)">Our certifications reflect Kestrada's commitment to the highest standards of quality, safety, and compliance. As a Service-Disabled Veteran-Owned Small Business (SDVOSB), we meet strict federal requirements and bring veteran values of discipline and integrity to every project. Being fully licensed, insured, OSHA compliant, and federally/state certified ensures that our clients can trust us to deliver construction solutions that are relia-ble, safe, and procurement-ready.</p>
<ul class="abs" style="left:628px;top:2574px;list-style:none;font-size:12.5px;color:var(--text);line-height:22.6px">
  <li><span class="bullet"></span>SDVOSB (Service-Disabled Veteran-Owned Small Business).</li>
  <li><span class="bullet"></span>Licensed &amp; Insured Contractor.</li>
  <li><span class="bullet"></span>OSHA &amp; Safety Compliant.</li>
  <li><span class="bullet"></span>Federal &amp; State Procurement Certified.</li>
</ul>

<!-- contact -->
<p class="abs center eyebrow" style="top:2792px">Contact Us</p>
<h2 class="abs center display section-title" style="top:2816px">Get In Touch With Us</h2>
<div class="abs underline" style="left:576px;top:2857px"></div>
<div class="abs field" style="left:255px;top:2889px;width:338px;height:40px">Enter Your First Name...</div>
<div class="abs field" style="left:606px;top:2889px;width:339px;height:40px">Enter Your Last Name...</div>
<div class="abs field" style="left:255px;top:2942px;width:338px;height:40px">Enter Your Email Address...</div>
<div class="abs field" style="left:606px;top:2942px;width:339px;height:40px">Enter Your Phone Number...</div>
<div class="abs field" style="left:255px;top:2994px;width:690px;height:86px">Please Send Your Message...</div>
<a class="abs btn" style="left:530px;top:3108px;width:138px;height:35px;font-size:12px">SUBMIT NOW</a>

<!-- footer -->
<footer class="abs" style="left:0;top:3233px;width:1200px;height:315px;background:var(--footer);color:var(--white)">
  <div class="abs brand" style="left:110px;top:92px;font-size:34px"><span class="dot" style="width:22px;height:22px"></span>Kestrada</div>
  <div class="abs" style="left:335px;top:47px;width:1px;height:178px;background:var(--footer-rule)"></div>
  <div class="abs" style="left:581px;top:47px;width:1px;height:178px;background:var(--footer-rule)"></div>
  <div class="abs" style="left:898px;top:47px;width:1px;height:178px;background:var(--footer-rule)"></div>
  <div class="abs footer-col" style="left:372px;top:58px">
    <p class="display footer-head">Quick Links</p>
    <p>Home</p><p>About Us</p><p>Services</p><p>Clients</p><p>Certifications</p><p>Contact Us</p>
  </div>
  <div class="abs footer-col" style="left:619px;top:58px">
    <p class="display footer-head">Contact</p>
    <p><svg width="10" height="12" viewBox="0 0 10 12" style="margin-right:8px"><path d="M5 0a4 4 0 0 1 4 4c0 3-4 8-4 8S1 7 1 4a4 4 0 0 1 4-4z" fill="#b88e33"/></svg>Lindenweg 18 10117 Berlin</p>
    <p><svg width="10" height="10" viewBox="0 0 10 10" style="margin-right:8px"><path d="M2 0l2 2-1 2 3 3 2-1 2 2-2 2C4 10 0 6 0 2z" fill="#b88e33"/></svg>(+321)555-0142</p>
    <p><svg width="11" height="8" viewBox="0 0 11 8" style="margin-right:8px"><rect width="11" height="8" fill="#b88e33"/><path d="M0 0l5.5 4L11 0" stroke="#0b0b0b" fill="none"/></svg>info@kestrada-build.example</p>
  </div>
  <div class="abs footer-col" style="left:936px;top:58px">
    <p class="display footer-head">Services</p>
    <p>General Contracting</p><p>Design-Build Construction</p><p>Environmental Remediation</p><p>Disaster Recovery</p>
  </div>
  <div class="abs" style="left:74px;top:267px;width:1051px;height:1px;background:var(--footer-rule)"></div>
  <p class="abs center" style="top:284px;font-size:12px">copyright © 2025 Kestrada.</p>
  <div class="abs" style="left:1140px;top:250px;width:40px;height:40px;border-radius:50%;background:var(--gold);display:flex;align-items:center;justify-content:center">
    <svg width="10" height="6" viewBox="0 0 10 6"><path d="M1 5l4-4 4 4" stroke="#fff" stroke-width="1.6" fill="none"/></svg>
  </div>
</footer>

</body>
</html>
```